Local Roofing/Construction company business needs new biz card design

We need a new business card design, current cards are from the start of this operation and generic at best. We are a local Construction Company (General Contractor) with a majority of our work originating from insurance claims-exterior finish work is the main focus (Roofs-Siding-Gutters etc). Heavily involved with homeowners and the low ball offers they receive from insurance company's after a insurable event takes place. I have attached some of our original logo file(s) below.

```html
<!DOCTYPE html>
<html lang="en">
<head>
<meta charset="utf-8">
<title>Ironline Construction — Business Card</title>
<link href="https://fonts.googleapis.com/css2?family=Lato:wght@400;700;900&display=swap" rel="stylesheet">
<style>
  :root {
    --page: #2a2d30;
    --card-dark: #0f1e22;
    --brand-green: #33db7d;
    --ink-light: #e9eeee;
    --ink-muted: #c9d2d2;
  }
  * { margin: 0; padding: 0; box-sizing: border-box; }
  html, body {
    width: 1200px; height: 952px; overflow: hidden;
    background: var(--page);
    font-family: "Lato", Arial, sans-serif;
  }
  .sheet {
    position: relative; width: 1200px; height: 952px;
    display: flex; flex-direction: column; align-items: center; justify-content: center; gap: 56px;
  }
  .card {
    position: relative; width: 600px; height: 343px;
    border-radius: 22px; overflow: hidden;
    background: var(--card-dark);
    box-shadow: 0 14px 30px rgba(0,0,0,.35);
  }

  /* Front */
  .card--front {
    display: flex; flex-direction: column; align-items: center; justify-content: center; gap: 22px;
    padding: 0 56px;
  }
  .brand-lockup { display: flex; align-items: center; gap: 14px; }
  .brand-mark { flex: none; width: 28px; height: 28px; background: var(--brand-green); border-radius: 4px; }
  .brand-name {
    font-weight: 900; font-size: 32px; letter-spacing: 1px; line-height: 1; white-space: nowrap;
    color: var(--brand-green); text-transform: uppercase;
  }
  .services {
    font-size: 16px; letter-spacing: 3px; color: var(--ink-light); text-transform: uppercase;
    display: flex; align-items: center; gap: 14px;
  }
  .services .dot { width: 7px; height: 7px; border-radius: 50%; background: var(--brand-green); }

  /* Back */
  .card--back .green-band { position: absolute; inset: 0; width: 100%; height: 100%; }
  .back-brand {
    position: absolute; left: 32px; top: 78px; width: 230px;
    font-weight: 900; font-size: 24px; line-height: 1.15; color: var(--card-dark);
    text-transform: uppercase; letter-spacing: .5px; white-space: nowrap;
  }
  .contact { position: absolute; left: 334px; top: 64px; width: 250px; }
  .contact__name {
    font-size: 21px; font-weight: 700; color: var(--brand-green); letter-spacing: .5px; text-transform: uppercase;
    white-space: nowrap;
  }
  .contact__role { font-size: 16px; color: var(--ink-muted); margin-top: 4px; margin-bottom: 22px; }
  .contact__list { list-style: none; display: flex; flex-direction: column; gap: 10px; }
  .contact__item { display: flex; align-items: flex-start; gap: 10px; font-size: 13.5px; color: var(--ink-light); line-height: 1.35; }
  .contact__icon {
    flex: none; width: 20px; height: 20px; border-radius: 4px;
    background: var(--ink-light); display: flex; align-items: center; justify-content: center;
  }
  .contact__icon--accent { background: var(--brand-green); }
  .contact__icon svg { width: 13px; height: 13px; }
</style>
</head>
<body>
<main class="sheet">

  <section class="card card--front" aria-label="Card front">
    <div class="brand-lockup">
      <span class="brand-mark"></span>
      <span class="brand-name">Ironline Construction</span>
    </div>
    <p class="services">
      <span>Roofs</span><span class="dot"></span><span>Siding</span><span class="dot"></span><span>Gutters</span>
    </p>
  </section>

  <section class="card card--back" aria-label="Card back">
    <svg class="green-band" viewBox="0 0 600 343" preserveAspectRatio="none" aria-hidden="true">
      <polygon points="0,0 300,0 300,50 210,343 0,343" fill="var(--brand-green)"/>
    </svg>
    <p class="back-brand">Ironline<br>Construction</p>

    <div class="contact">
      <p class="contact__name">Daniel M. Porter</p>
      <p class="contact__role">General Contractor</p>
      <ul class="contact__list">
        <li class="contact__item">
          <span class="contact__icon contact__icon--accent">
            <svg viewBox="0 0 12 12"><path d="M6 1a3.5 3.5 0 0 0-3.5 3.5C2.5 7.3 6 11 6 11s3.5-3.7 3.5-6.5A3.5 3.5 0 0 0 6 1zm0 4.8a1.3 1.3 0 1 1 0-2.6 1.3 1.3 0 0 1 0 2.6z" fill="#0f1e22"/></svg>
          </span>
          <span>1250 Ridgeview Avenue<br>Springfield, DC 20031</span>
        </li>
        <li class="contact__item">
          <span class="contact__icon">
            <svg viewBox="0 0 12 12"><path d="M3 1.5l1.6 2.2-.9 1.1c.6 1.3 1.3 2 2.5 2.5l1.1-.9 2.2 1.6-.7 1.7C5.4 9.5 2.5 6.6 1.3 2.2z" fill="#0f1e22"/></svg>
          </span>
          <span>+00 555 210 44</span>
        </li>
        <li class="contact__item">
          <span class="contact__icon">
            <svg viewBox="0 0 12 12"><rect x="1.5" y="3" width="9" height="6" fill="none" stroke="#0f1e22" stroke-width="1.2"/><path d="M1.5 3L6 6.6 10.5 3" fill="none" stroke="#0f1e22" stroke-width="1.2"/></svg>
          </span>
          <span>office@ironlinebuild.com</span>
        </li>
        <li class="contact__item">
          <span class="contact__icon">
            <svg viewBox="0 0 12 12"><path d="M3 2l6 3.2-2.6.8 1.8 3.2-1.1.6-1.8-3.2L3.5 8.3z" fill="#0f1e22"/></svg>
          </span>
          <span>www.ironlinebuild.com</span>
        </li>
      </ul>
    </div>
  </section>

</main>
</body>
</html>
```